Heritage Hollow Business Cards

Require a business card design. <br/><br/>Needs to include logo (either round or long version) plus these details:<br/>Maya Torvell<br/>Heritage Hollow<br/>maya@kelvadtrading.com.au<br/>02 6481 7395<br/>PO Box Glenwarra NSW 2791<br/>www.heritagehollow.com.au<br/><br/>I need in an editable format so that I can create for multiple staff members. <br/><br/>

Target Market(s)

We are an online store selling renovation products to home owners are builders. Looking for a classic classy design.

Industry/Entity Type

Home And Garden

Contact Information for Business Card

Maya Torvell
Heritage Hollow
maya@kelvadtrading.com.au
02 6481 7395
PO Box Glenwarra NSW 2791
www.heritagehollow.com.au

Colors

Designer to choose colors to be used in the design.

Requirements
Must have
• Must include Logo.

```html
<!DOCTYPE html>
<html lang="en">
<head>
<meta charset="utf-8">
<title>Heritage Hollow Business Cards</title>
<link href="https://fonts.googleapis.com/css2?family=Montserrat:wght@400;500&display=swap" rel="stylesheet">
<style>
  :root {
    --stage: #d8d2c8;
    --card-light: #ffffff;
    --card-dark: #0c0c0d;
    --card-dark-edge: #1d1d1f;
    --ink: #1b1b1b;
    --ink-soft: #3a3a3a;
    --rule: #7d8384;
    --mark-line: #555555;
    --on-dark: #f2f2f2;
    --font-text: "Montserrat", Arial, sans-serif;
  }
  html, body {
    margin: 0;
    padding: 0;
    width: 1200px;
    height: 859px;
    overflow: hidden;
    background: var(--stage);
    font-family: var(--font-text);
  }
  .canvas {
    position: relative;
    width: 1200px;
    height: 859px;
  }
  .card {
    position: absolute;
    top: 289px;
    width: 500px;
    height: 285px;
    border-radius: 12px;
    overflow: hidden;
    box-shadow: 0 10px 24px rgba(0,0,0,0.28);
  }
  .card--front {
    left: 60px;
    background: var(--card-light);
    color: var(--ink);
  }
  .card--back {
    left: 640px;
    background: var(--card-dark);
  }

  /* brand lockup: plain circle beside the name */
  .brand {
    position: absolute;
    display: flex;
    align-items: center;
    gap: 10px;
    white-space: nowrap;
  }
  .brand__dot {
    border-radius: 50%;
    border: 1.5px solid currentColor;
    box-sizing: border-box;
  }
  .brand__name {
    font-weight: 500;
    letter-spacing: 0.01em;
  }
  .card--front .brand {
    left: 50%;
    top: 60px;
    transform: translateX(-50%);
    color: var(--ink);
  }
  .card--front .brand__dot { width: 34px; height: 34px; border-color: var(--mark-line); }
  .card--front .brand__name { font-size: 24px; }

  .front__rule {
    position: absolute;
    left: 23px;
    right: 23px;
    top: 162px;
    height: 1.5px;
    background: var(--rule);
  }
  .front__accent {
    position: absolute;
    left: 23px;
    bottom: 0;
    width: 118px;
    height: 3px;
    background: var(--ink-soft);
  }
  .person {
    position: absolute;
    left: 24px;
    top: 184px;
    margin: 0;
    font-size: 23px;
    font-weight: 500;
    color: var(--ink);
  }
  .contact {
    position: absolute;
    right: 23px;
    top: 185px;
    margin: 0;
    padding: 0;
    list-style: none;
    text-align: right;
    font-size: 12.5px;
    line-height: 17.5px;
    color: var(--ink-soft);
  }
  .contact__address { margin-bottom: 8px; padding-right: 0; }
  .contact__item {
    display: flex;
    justify-content: flex-end;
    align-items: center;
    gap: 6px;
  }
  .contact__icon { width: 12px; height: 12px; flex: none; }

  .back__texture {
    position: absolute;
    inset: 0;
    background: radial-gradient(ellipse at 50% 40%, #2a2a2c 0%, var(--card-dark-edge) 45%, var(--card-dark) 100%);
  }
  .card--back .brand {
    left: 50%;
    top: 50%;
    transform: translate(-50%, -50%);
    color: var(--on-dark);
  }
  .card--back .brand__dot { width: 44px; height: 44px; }
  .card--back .brand__name { font-size: 30px; }
</style>
</head>
<body>
<main class="canvas">

  <section class="card card--front" aria-label="Business card front">
    <div class="brand">
      <span class="brand__dot"></span>
      <span class="brand__name">Heritage Hollow</span>
    </div>
    <div class="front__rule"></div>
    <h1 class="person">Maya Torvell</h1>
    <ul class="contact">
      <li class="contact__address">PO Box Glenwarra NSW 2791</li>
      <li class="contact__item">02 6481 7395
        <svg class="contact__icon" viewBox="0 0 12 12" aria-hidden="true">
          <circle cx="6" cy="6" r="5" fill="none" stroke="#1b1b1b" stroke-width="1.1"/>
          <path d="M4.2 3.6c.3-.2.6-.1.7.2l.3.7c.1.2 0 .4-.2.5l-.3.2c.3.7.8 1.2 1.5 1.5l.2-.3c.1-.2.3-.3.5-.2l.7.3c.3.1.4.4.2.7-.3.5-.8.7-1.3.6-1.4-.4-2.5-1.5-2.9-2.9-.1-.5.1-1 .6-1.3z" fill="#1b1b1b"/>
        </svg>
      </li>
      <li class="contact__item">maya@kelvadtrading.com.au
        <svg class="contact__icon" viewBox="0 0 12 12" aria-hidden="true">
          <rect x="1" y="2.5" width="10" height="7" fill="none" stroke="#1b1b1b" stroke-width="1.1"/>
          <path d="M1 2.8 6 6.6 11 2.8" fill="none" stroke="#1b1b1b" stroke-width="1.1"/>
        </svg>
      </li>
      <li class="contact__item">www.heritagehollow.com.au
        <svg class="contact__icon" viewBox="0 0 12 12" aria-hidden="true">
          <circle cx="6" cy="6" r="5" fill="#1b1b1b"/>
          <path d="M1 6h10M6 1v10M6 1c-2.2 2.6-2.2 7.4 0 10M6 1c2.2 2.6 2.2 7.4 0 10M2 3.5h8M2 8.5h8" fill="none" stroke="#ffffff" stroke-width="0.6"/>
        </svg>
      </li>
    </ul>
    <div class="front__accent"></div>
  </section>

  <section class="card card--back" aria-label="Business card back">
    <div class="back__texture" role="img" aria-label="Faint sketched roof truss and timber framing drawing across the dark background"></div>
    <div class="brand">
      <span class="brand__dot"></span>
      <span class="brand__name">Heritage Hollow</span>
    </div>
  </section>

</main>
</body>
</html>
```